Candle Rental Business seeks new website design

We need a new website design for a Candle hire business. The business rents out pillar candles for events such as weddings and corporate events. Our main target market is weddings. The business name is Hire a Lantern. The business name does not have a logo design.

We would like a website that is light in colours and creates a warm atmosphere. The design needs to be elegant and upmarket. There are different size candles that we hire out, ranging from 10cm diameter to 20cm diameter, flat, tall etc. All our candles are white in colour. Its just the size that differs.

We would also like to include a section for hiring out decor such as glassvases, candlebras, overlays and chairs sachets, chair covers. However, this is not the businesses main focus but an additional offering to customers.

Target Market(s)

Wedding venues and brides. Corporate events. School dances.

Industry/Entity Type

Hospitality

Logo Text

Hire a Lantern

Number of Pages Required

1 page

Font styles to use
Sans Serif
Script

Requirements
Must have
• Pictures of pillar candles. Plain white candles. The website must centre around candles.
Nice to have
• Different examples of candle centrepieces
Should not have
• Pictures must not be of brides. Pictures of surrounding is perferable.

```html
<!DOCTYPE html>
<html lang="en">
<head>
<meta charset="utf-8">
<title>Hire a Lantern</title>
<link href="https://fonts.googleapis.com/css2?family=Marcellus&family=Open+Sans:wght@400;600&family=Raleway:wght@500;600&display=swap" rel="stylesheet">
<style>
:root{
  --purple:#7b1fa8;
  --purple-dark:#5a1480;
  --magenta:#9c1f8c;
  --yellow:#f7c400;
  --orange:#f0a000;
  --title-orange:#e89000;
  --ink:#222;
  --brand-ink:#3a3a3a;
  --body:#666;
  --light:#888;
  --footer:#ebebeb;
  --white:#fff;
}
*{box-sizing:border-box;margin:0;padding:0}
html,body{width:1200px;height:2187px;overflow:hidden}
body{position:relative;background:var(--white);font-family:"Open Sans",sans-serif;color:var(--body)}
.abs{position:absolute}
.top-bg{left:0;top:0;width:1200px;height:573px;background:linear-gradient(180deg,#f2f2f2,#e6e6e6)}
.brand{left:138px;top:46px;font-family:"Raleway",sans-serif;font-weight:600;font-size:32px;line-height:44px;color:var(--brand-ink);letter-spacing:.3px}
.ribbon{left:80px;top:141px;width:1040px;height:56px}
.nav{left:133px;top:117px;width:936px;height:51px;background:var(--purple);display:flex;align-items:center}
.nav a{font-family:"Raleway",sans-serif;font-weight:600;font-size:16px;color:var(--white);text-decoration:none;text-transform:uppercase;height:100%;display:flex;align-items:center;justify-content:center}
.nav a.active{background:linear-gradient(180deg,#ffd400,#f2b800);width:134px}
.nav a.item{padding:0 23px}
.hero{left:133px;top:168px;width:936px;height:405px;background:radial-gradient(ellipse at 70% 45%,#d8c3a0 0%,#8a7a6a 35%,#4a4650 70%,#3a3a44 100%)}
.hero-caption{left:133px;top:365px;width:457px;height:112px;background:rgba(60,60,60,.72);padding:20px 28px;font-family:"Marcellus",serif;font-size:28px;line-height:38px;color:var(--white);text-transform:uppercase}
.dots{left:559px;top:539px;display:flex;gap:5px}
.dots span{width:17px;height:17px;border-radius:50%;background:var(--white)}
.dots span.on{background:var(--yellow);border:3px solid var(--white)}
.section-title{left:0;width:1200px;text-align:center;font-family:"Marcellus",serif;font-size:32px;display:flex;justify-content:center;align-items:center;gap:22px}
.section-title .rule{width:44px;height:2px;background:#ccc}
.purple{color:var(--purple)}
.orange{color:var(--orange)}
.candle-card{width:232px;text-align:center}
.candle-ring{margin:0 auto;width:216px;height:216px;border-radius:50%;border:1px solid #ddd;display:flex;align-items:center;justify-content:center}
.candle-photo{width:194px;height:194px;border-radius:50%;background:radial-gradient(circle,#ffffff 20%,#ececec 60%,#fafafa 100%)}
.card-title{margin-top:12px;font-size:17px;color:var(--title-orange)}
.card-text{margin-top:2px;font-size:13px;line-height:17px;color:var(--light)}
.about-band{left:0;top:990px;width:1200px;height:410px;background:radial-gradient(ellipse at 45% 50%,#ffffff 0%,#f3f3f3 55%,#e4e4e4 100%)}
.about-title{left:146px;top:1066px;font-family:"Marcellus",serif;font-weight:400;font-size:40px;color:var(--ink)}
.about-lead{left:141px;top:1128px;width:500px;font-size:15px;line-height:21px;color:#555}
.about-body{left:141px;top:1186px;width:500px;font-size:13.5px;line-height:21px;color:var(--light)}
.btn-outline{left:141px;top:1292px;width:111px;height:32px;border:2px solid var(--magenta);box-shadow:inset 0 0 0 2px var(--white);background:var(--magenta);color:var(--white);font-size:11px;display:flex;align-items:center;justify-content:center;text-transform:uppercase}
.about-photo{left:700px;top:1020px;width:360px;height:380px;background:linear-gradient(180deg,rgba(255,255,255,0) 0%,rgba(225,225,225,.5) 55%,rgba(70,70,70,.3) 100%)}
.product{width:229px;text-align:center}
.product-photo{width:229px;height:179px}
.product-title{margin-top:16px;font-family:"Raleway",sans-serif;font-weight:500;font-size:17px;color:var(--ink)}
.product-text{margin-top:4px;font-size:11px;line-height:16px;color:var(--light)}
.btn-solid{margin:12px auto 0;width:96px;height:28px;background:var(--orange);color:var(--white);font-size:10.5px;display:flex;align-items:center;justify-content:center;text-transform:uppercase}
.footer-wave{left:0;top:1825px;width:1200px;height:310px}
.footer-col{top:1916px}
.footer-col h4{font-family:"Raleway",sans-serif;font-weight:500;font-size:19px;color:#444;margin-bottom:10px}
.footer-col li{list-style:none;font-size:12px;line-height:25.5px;color:#555}
.footer-divider{top:1920px;width:1px;height:170px;background:#dcdcdc}
.social{display:flex;gap:5px;margin-top:4px}
.social span{width:29px;height:29px;border-radius:50%;border:2px solid #222}
.legal{left:0;top:2128px;width:1200px;height:59px;background:var(--white);border-top:1px solid #ddd;padding:16px 0 0 139px;font-size:11.5px;color:var(--light)}
</style>
</head>
<body>
<div class="abs top-bg"></div>

<div class="abs brand">Hire a Lantern</div>

<svg class="abs ribbon" viewBox="0 0 1040 56" aria-hidden="true">
  <polygon points="0,0 53,0 53,56 0,56 22,28" fill="var(--purple)"/>
  <polygon points="987,0 1040,0 1018,28 1040,56 987,56" fill="var(--purple)"/>
  <polygon points="53,27 53,56 40,27" fill="var(--purple-dark)"/>
  <polygon points="987,27 987,56 1000,27" fill="var(--purple-dark)"/>
</svg>

<nav class="abs nav">
  <a class="active">Home</a>
  <a class="item">About Us</a>
  <a class="item">Candel on Rent</a>
  <a class="item">Our Products</a>
  <a class="item">Hiring</a>
  <a class="item">Contact Us</a>
</nav>

<div class="abs hero" role="img" aria-label="Lit white pillar candles in glass hurricane vases on a table"></div>
<div class="abs hero-caption">Hiring Wedding Candel<br>&amp; Product on Rent</div>
<div class="abs dots"><span class="on"></span><span></span><span></span><span></span></div>

<h2 class="abs section-title purple" style="top:596px;font-weight:400"><span class="rule"></span>Our Candels<span class="rule"></span></h2>

<div class="abs candle-card" style="left:125px;top:652px">
  <div class="candle-ring"><div class="candle-photo" role="img" aria-label="Single white pillar candle"></div></div>
  <div class="card-title">Candel Tittle</div>
  <div class="card-text">ongue augue et malesuada iaculis<br>ipsum dui aliquet felis at</div>
</div>
<div class="abs candle-card" style="left:358px;top:652px">
  <div class="candle-ring"><div class="candle-photo" role="img" aria-label="Bundle of tall white taper candles"></div></div>
  <div class="card-title">Candel Tittle</div>
  <div class="card-text">ongue augue et malesuada iaculis<br>ipsum dui aliquet felis at</div>
</div>
<div class="abs candle-card" style="left:593px;top:652px">
  <div class="candle-ring"><div class="candle-photo" role="img" aria-label="Group of ivory pillar candles of different heights"></div></div>
  <div class="card-title">Candel Tittle</div>
  <div class="card-text">ongue augue et malesuada iaculis<br>ipsum dui aliquet felis at</div>
</div>
<div class="abs candle-card" style="left:826px;top:652px">
  <div class="candle-ring"><div class="candle-photo" role="img" aria-label="White candles in glass cylinder holders"></div></div>
  <div class="card-title">Candel Tittle</div>
  <div class="card-text">ongue augue et malesuada iaculis<br>ipsum dui aliquet felis at</div>
</div>

<div class="abs about-band"></div>
<h2 class="abs about-title">About Hire a Lantern</h2>
<p class="abs about-lead">Curabitur iaculis tempus eros Curabitur vel mi sit amet magna malesuada ultrices Ut nisi erat fermentum</p>
<p class="abs about-body">Morbi ornare gravida elit Integer congue augue et malesuada iaculis ipsum dui aliquet felis at cursus magna nisl nec elit Praesent elementum elit at tellus nec ultricies sit amet porttitor mattis enim In massa libero interdum nec interdum vel blandit sed nulla In ullamcorper est eget tempor cursus n</p>
<div class="abs btn-outline">Click Here</div>
<div class="abs about-photo" role="img" aria-label="Three white pillar candles on black wooden candlesticks"></div>

<h2 class="abs section-title orange" style="top:1427px;font-weight:400"><span class="rule"></span>Other Products<span class="rule"></span></h2>

<div class="abs product" style="left:128px;top:1490px">
  <div class="product-photo" role="img" aria-label="Tea lights glowing in glass holders" style="background:radial-gradient(circle at 50% 60%,#c07a30,#3a2010 70%,#140a05)"></div>
  <div class="product-title">Overlays</div>
  <div class="product-text">Mauris vel lacus vitae felis vestibulum<br>volutpat imperdiet ac nisl</div>
  <div class="btn-solid">Click Here</div>
</div>
<div class="abs product" style="left:366px;top:1490px">
  <div class="product-photo" role="img" aria-label="Pink tulips in small glass vases" style="background:linear-gradient(180deg,#e6e8e4,#c9cfc6 60%,#a9aea4)"></div>
  <div class="product-title">Glassvases</div>
  <div class="product-text">Mauris vel lacus vitae felis vestibulum<br>volutpat imperdiet ac nisl</div>
  <div class="btn-solid">Click Here</div>
</div>
<div class="abs product" style="left:604px;top:1490px">
  <div class="product-photo" role="img" aria-label="Dessert table with cupcakes and pastel decor" style="background:linear-gradient(180deg,#f1e6ea,#e4d6d2 60%,#cfc3bd)"></div>
  <div class="product-title">Candel Bars</div>
  <div class="product-text">Mauris vel lacus vitae felis vestibulum<br>volutpat imperdiet ac nisl</div>
  <div class="btn-solid">Click Here</div>
</div>
<div class="abs product" style="left:841px;top:1490px">
  <div class="product-photo" role="img" aria-label="White chairs dressed with purple satin sashes" style="background:linear-gradient(135deg,#ecebf2,#b9a6d2 55%,#6a3c9c)"></div>
  <div class="product-title">Chairs sachets</div>
  <div class="product-text">Mauris vel lacus vitae felis vestibulum<br>volutpat imperdiet ac nisl</div>
  <div class="btn-solid">Click Here</div>
</div>

<svg class="abs footer-wave" viewBox="0 0 1200 310" preserveAspectRatio="none" aria-hidden="true">
  <path d="M0,28 C300,50 800,40 1200,0 L1200,310 L0,310 Z" fill="var(--footer)"/>
</svg>

<div class="abs footer-col" style="left:140px"><h4>Quick Links</h4><ul><li>Natoque penatibus</li><li>Et magnis</li><li>Dis parturient</li><li>Montes nascetur</li><li>Ridiculus mus In</li></ul></div>
<div class="abs footer-divider" style="left:281px"></div>
<div class="abs footer-col" style="left:319px"><h4>Best Venues</h4><ul><li>Etiam est nunc</li><li>Venenatis</li><li>Tristique eu</li><li>Imperdiet ac nisl</li><li>Cum sociis</li></ul></div>
<div class="abs footer-divider" style="left:465px"></div>
<div class="abs footer-col" style="left:502px"><h4>Resources</h4><ul><li>Natoque penatibus</li><li>Et magnis</li><li>Dis parturient</li><li>Montes nascetur</li><li>Ridiculus mus In</li></ul></div>
<div class="abs footer-divider" style="left:637px"></div>
<div class="abs footer-col" style="left:672px"><h4>Support</h4><ul><li>Natoque penatibus</li><li>Et magnis</li><li>Dis parturient</li><li>Montes nascetur</li><li>Ridiculus mus In</li></ul></div>
<div class="abs footer-divider" style="left:807px"></div>
<div class="abs footer-col" style="left:838px;top:1913px"><h4>Get in touch</h4><div class="social"><span></span><span></span><span></span><span></span></div></div>

<div class="abs legal">© 2016 Company Name &nbsp;All right reserved &nbsp;Term of Use</div>
</body>
</html>
```